Webdesign für Heilpraktiker
Zielgruppe
Ich bin Heilpraktiker und betreibe eine Naturheilpraxis mit den Schwerpunkten der traditionellen chinesischen Medizin (TCM). Da ganz besonders in der Philosophie (sogenannte 'Schule' des Wo Shen). Aber auch in der traditionellen Heilweise der TCM, wie Akupunktur, Heilkräutermedizin und weiteres.
Die Zielgruppe sind Menschen, die medizinische Hilfe benötigen. (Vom Kind bis zum älteren Menschen).
Aufgabenstellung
Es gibt ein Praxislogo, ein Foto von mir und ggf. ein Landschaftsbild. Ich dachte an fünf Hauptseiten mit Untergruppen. Am Ende sollte alles in Wordpress formatiert werden können, um es zu veröffentlichen.
Weitere Fotos zur Unterstützung der Themen kann ich natürlich gerne liefern.
Die Gestaltung ist nicht festgesetzt. Sollte aber seriös rüber kommen.

```html
<!DOCTYPE html>
<html lang="de">
<head>
<meta charset="utf-8">
<title>Naturheilpraxis Fellnroth – Zu meiner Person</title>
<link rel="stylesheet" href="https://fonts.googleapis.com/css2?family=Cormorant+Garamond:wght@500&family=Lato:wght@400&family=Open+Sans:ital,wght@0,400;1,400&display=swap">
<style>
  :root {
    --paper: #f1efea;
    --paper-deep: #ebe7e0;
    --ink: #3a3836;
    --heading: #4a4744;
    --gold: #c9a153;
    --gold-light: #d3ae66;
    --quote: #f6efdf;
    --footer: #2b2624;
    --footer-text: #f2f0ec;
    --leaf: #8fba3a;
    --leaf-dark: #6e8f3a;
  }
  * { margin: 0; padding: 0; box-sizing: border-box; }
  html, body { width: 1200px; height: 3358px; overflow: hidden; }
  body {
    position: relative;
    background: var(--paper);
    color: var(--ink);
    font-family: "Lato", sans-serif;
  }
  .abs { position: absolute; }
  .center-x { transform: translateX(-50%); text-align: center; white-space: nowrap; }

  /* Header */
  .brand { left: 600px; top: 40px; display: flex; align-items: center; gap: 14px; transform: translateX(-50%); }
  .brand-mark { width: 22px; height: 22px; border-radius: 50%; background: var(--gold); }
  .brand-name { font-family: "Lato", sans-serif; font-size: 26px; letter-spacing: 2px; color: var(--ink); white-space: nowrap; }
  .main-nav { left: 600px; top: 167px; transform: translateX(-50%); display: flex; gap: 24px;
    font-family: "Open Sans", sans-serif; font-size: 18px; color: #1f1d1b; white-space: nowrap; }
  .main-nav a { color: inherit; text-decoration: none; }

  /* Hero */
  .hero-photo { left: 0; top: 225px; width: 582px; height: 398px;
    background: radial-gradient(ellipse at 40% 45%, var(--leaf) 0%, #9cc24a 40%, var(--leaf-dark) 100%); }
  .hero-quote-band { left: 582px; top: 271px; width: 618px; height: 352px;
    background: linear-gradient(160deg, var(--gold-light), var(--gold) 60%, #c39a4d); }
  .quote-text { left: 896px; top: 370px; font-family: "Open Sans", sans-serif; font-size: 22px; line-height: 38px; color: var(--quote); }
  .quote-mark { font-family: "Cormorant Garamond", serif; font-size: 26px; line-height: 0; vertical-align: 8px; }
  .quote-mark.open { margin-right: 4px; }
  .quote-mark.close { margin-left: 3px; }
  .quote-source { left: 958px; top: 470px; font-family: "Open Sans", sans-serif; font-style: italic; font-size: 20px; color: var(--quote); }

  /* Headings & copy */
  .section-title { font-family: "Cormorant Garamond", serif; font-weight: 500; font-size: 36px; letter-spacing: 1px; color: var(--heading); }
  .copy { font-size: 16.5px; line-height: 29px; color: var(--ink); }
  .copy-wide { line-height: 31px; }

  /* Person */
  .portrait { left: 825px; top: 645px; width: 302px; height: 453px;
    background: linear-gradient(180deg, #6a6d72 0%, #4b4e54 45%, #2a2c33 100%); }
  .signature { left: 251px; top: 1015px; width: 277px; height: 60px; background: linear-gradient(90deg, rgba(58,56,54,0.12), rgba(58,56,54,0.22), rgba(58,56,54,0.12)); border-radius: 30px; }

  /* Topics band */
  .topics-band { left: 0; top: 1127px; width: 1200px; height: 1277px;
    background: linear-gradient(180deg, var(--paper-deep), #e9e4dc 50%, var(--paper-deep)); }
  .topic-photo { border-radius: 50%; }
  .photo-tcm { left: 199px; top: 1224px; width: 212px; height: 212px; background: radial-gradient(circle at 45% 50%, #e7e1d7 0%, #b9a894 45%, #6d4a33 100%); }
  .photo-water { left: 873px; top: 1553px; width: 216px; height: 216px; background: radial-gradient(circle at 50% 40%, #c9a08a 0%, #8c8a82 50%, #4f5553 100%); }
  .photo-seedling { left: 184px; top: 1913px; width: 216px; height: 216px; background: radial-gradient(circle at 45% 55%, #79a33a 0%, #5f7d43 45%, #3f4a36 100%); box-shadow: 0 4px 10px rgba(0,0,0,0.18); }

  /* Landscape & footer */
  .landscape { left: 0; top: 2767px; width: 1200px; height: 251px;
    background: linear-gradient(180deg, #dfe3e2 0%, #a7b6a3 25%, #7fa04a 55%, #6f9a38 100%); }
  .site-footer { left: 0; top: 3018px; width: 1200px; height: 340px; background: var(--footer); }
  .footer-badge { left: 544px; top: 3052px; width: 174px; height: 174px; border-radius: 50%; background: #fbfaf8;
    display: flex; align-items: center; justify-content: center; text-align: center; }
  .footer-badge span { font-size: 17px; letter-spacing: 1px; color: var(--ink); line-height: 24px; }
  .footer-nav { left: 627px; top: 3298px; font-family: "Open Sans", sans-serif; font-size: 21px; color: var(--footer-text); }
  .footer-nav a { color: inherit; text-decoration: none; margin: 0 7px; }
</style>
</head>
<body>

<header>
  <div class="abs brand">
    <span class="brand-mark"></span>
    <span class="brand-name">PRAXIS FELLNROTH</span>
  </div>
  <nav class="abs main-nav" aria-label="Hauptnavigation">
    <a>STARTSEITE</a>
    <a>ZU MEINER PERSON</a>
    <a>WOBEI KANN ICH HELFEN</a>
    <a>WAS IST DAS WO SHEN</a>
    <a>KONTAKT</a>
  </nav>
</header>

<section class="hero">
  <div class="abs hero-photo" role="img" aria-label="Foto: grüne Baumkrone mit verschlungenen Ästen"></div>
  <div class="abs hero-quote-band"></div>
  <p class="abs quote-text center-x">
    <span class="quote-mark open">“</span>Die Zweige geben Kunde<br>
    von der Wurzel.<span class="quote-mark close">”</span>
  </p>
  <p class="abs quote-source center-x">Volksweisheit / Volksgut</p>
</section>

<section class="person">
  <h1 class="abs section-title center-x" style="left:383px; top:705px;">ZU MEINER PERSON</h1>
  <p class="abs copy center-x" style="left:390px; top:772px;">
    Als Heilpraktiker und TCM - der traditionellen chinesischen Medizin, ist die<br>
    Behandlung eines Patienten ohne diesen Möglichkeiten<br>
    für mich schon lange nicht mehr vorstellbar.<br>
    Lorem ipsum dolor sit amet, consectetur adipiscing elit, sed do eiusmod<br>
    tempor incididunt ut labore et dolore magna aliqua. Quis ipsum suspendisse<br>
    ultrices gravida. Risus commodo viverra maecenas accumsan lacus vel facilisis.
  </p>
  <p class="abs copy center-x" style="left:390px; top:976px; font-size:19px;">Ihr</p>
  <div class="abs signature" role="img" aria-label="Handschriftliche Unterschrift Konrad Fellnroth"></div>
  <div class="abs portrait" role="img" aria-label="Porträtfoto des Heilpraktikers im dunklen Sakko"></div>
</section>

<section class="topics">
  <div class="abs topics-band"></div>

  <div class="abs topic-photo photo-tcm" role="img" aria-label="Foto: Akupunkturkopf mit Meridianpunkten"></div>
  <h2 class="abs section-title center-x" style="left:791px; top:1216px;">WARUM TCM?</h2>
  <p class="abs copy copy-wide center-x" style="left:778px; top:1283px;">
    Die Harmonie des Körpers wird wieder hergestellt und findet sich<br>
    mit TCM im Glkeichgewicht&nbsp; wieder.&nbsp; Somit können Kräfte wieder aktiviert<br>
    werden.
  </p>

  <h2 class="abs section-title center-x" style="left:448px; top:1557px;">MEINE BEWEGGRÜNDE</h2>
  <p class="abs copy copy-wide center-x" style="left:470px; top:1633px;">
    Lorem ipsum dolor sit amet, consectetur adipiscing elit, sed do eiusmod tempor<br>
    incididunt ut labore et dolore magna aliqua. Quis ipsum suspendisse ultrices<br>
    gravida. Risus commodo viverra maecenas accumsan lacus vel facilisis.
  </p>
  <div class="abs topic-photo photo-water" role="img" aria-label="Foto: Hände schöpfen Wasser"></div>

  <div class="abs topic-photo photo-seedling" role="img" aria-label="Foto: junger Setzling wird gegossen"></div>
  <h2 class="abs section-title center-x" style="left:724px; top:1912px;">VITA</h2>
  <p class="abs copy copy-wide center-x" style="left:722px; top:1968px;">
    Lorem ipsum dolor sit amet, consectetur adipiscing elit, sed do eiusmod tempor<br>
    incididunt ut labore et dolore magna aliqua. Quis ipsum suspendisse ultrices<br>
    gravida. Risus commodo viverra maecenas accumsan lacus vel facilisis.
  </p>
</section>

<section class="membership">
  <h2 class="abs section-title center-x" style="left:603px; top:2484px; font-size:28px;">MITGLIEDSCHAFT</h2>
</section>

<div class="abs landscape" role="img" aria-label="Landschaftsfoto: grüne Hügel unter weitem Himmel"></div>

<footer class="abs site-footer"></footer>
<div class="abs footer-badge"><span>PRAXIS<br>FELLNROTH</span></div>
<nav class="abs footer-nav center-x" aria-label="Rechtliches">
  <a>IMPRESSUM</a><a>DATENSCHUTZ</a>
</nav>

</body>
</html>
```